Poster Design Project

About Us
Vexora is a company that specializes in providing communication solutions to the travel market. Our simple vision of “every hotel should have a mobile phone in the guest rooms”, led us to develop a path breaking cost effective mobile phone. With full integration capabilities with the hotels property management system, location based marketing, user locator and other features, this product is unique in addressing the hospitality segment.
Product Placement
The Vexora mobile will be placed in the hotel room on an A4 Sized transparent stand (the transparent stand is attached for your reference. If you notice, the phone will be placed in the jacket on the bottom left and in another jacket on the bottom right will be the brochure. So effectively, the design space available on the A4 brochure is only 60% of the space). The designed poster that we wish designed will be inserted in the A4 sized acrylic stand. The stand would typically be on the bedside table or on the study table of the hotel room. The A4 design should be bright and vibrant in keeping with our logo colors.
Attached is our logo. Also attached is the symbol of our phone that could be used innovatively on the brochure if you think it helps.
Attached is the content for the poster.
Updates
Project Deadline Extended
Reason: Feedback from the management team got delayed, hence the extension. Thanks
Project Deadline Extended
Reason: The delay is in the content finalization.
Industry/Entity Type
Property Management
Look and feel
Each slider illustrates characteristics of the customer's brand and the style your logo design should communicate.

```html
<!DOCTYPE html>
<html lang="en">
<head>
<meta charset="utf-8">
<title>Vexora – Keep Talking poster</title>
<link rel="stylesheet" href="https://fonts.googleapis.com/css2?family=Roboto:wght@300;400&family=Roboto+Condensed:wght@300;400;700&display=swap">
<style>
  :root {
    --page: #ffffff;
    --peach-light: #fde8d0;
    --peach-mid: #fdc894;
    --orange-deep: #fb8f22;
    --orange-box: #fb8c1e;
    --orange-dots: #f7a44a;
    --ink: #2f2f33;
    --operator: #9c9c9c;
    --white: #ffffff;
  }
  * { margin: 0; padding: 0; box-sizing: border-box; }
  html, body {
    width: 1170px; height: 1200px; overflow: hidden;
    background: var(--page);
  }
  .canvas { position: relative; width: 1170px; height: 1200px; }

  .poster {
    position: absolute; left: 191px; top: 55px; width: 742px; height: 1053px;
    background: linear-gradient(135deg, var(--peach-light) 0%, #fde0bf 35%, var(--peach-mid) 70%, var(--orange-deep) 100%);
    overflow: visible;
  }

  .brand { position: absolute; left: 42px; top: 30px; display: flex; align-items: center; gap: 16px; }
  .brand-mark { width: 106px; height: 106px; border-radius: 50%; background: var(--orange-box); }
  .brand-name {
    font-family: "Roboto Condensed", sans-serif; font-weight: 700;
    font-size: 40px; color: var(--ink); letter-spacing: -0.5px;
  }

  .world-map {
    position: absolute; left: 12px; top: 153px; width: 732px; height: 350px;
    border-radius: 40% 45% 35% 40%;
    background: radial-gradient(ellipse at 50% 45%, rgba(247,164,74,0.55) 0%, rgba(247,164,74,0.35) 55%, rgba(247,164,74,0) 80%);
  }

  .headline {
    position: absolute; left: 89px; top: 262px;
    font-family: "Roboto", sans-serif; font-weight: 300;
    font-size: 37px; line-height: 47px; color: var(--ink); letter-spacing: -0.5px;
  }

  .offer { position: absolute; top: 474px; left: 0; width: 100%; height: 160px; }
  .offer-box {
    position: absolute; top: 0; height: 160px;
    background: var(--orange-box); border-radius: 4px;
    padding: 10px 7px; color: var(--white);
    font-family: "Roboto Condensed", sans-serif;
  }
  .offer-box strong { display: block; font-weight: 700; font-size: 23px; line-height: 29px; }
  .offer-box span { display: block; font-weight: 300; font-size: 18px; line-height: 24px; }
  .box-save { left: 45px; width: 114px; }
  .box-local { left: 193px; width: 89px; }
  .box-intl { left: 317px; width: 114px; }
  .box-localmin { left: 465px; width: 89px; }
  .box-price { left: 588px; width: 114px; text-align: center; }
  .operator {
    position: absolute; top: 50px;
    font-family: "Roboto", sans-serif; font-weight: 400;
    font-size: 44px; line-height: 40px; color: var(--operator);
  }
  .op-1 { left: 162px; } .op-2 { left: 285px; } .op-3 { left: 433px; } .op-4 { left: 557px; }

  .features {
    position: absolute; left: 42px; top: 685px; list-style: none;
    font-family: "Roboto", sans-serif; font-size: 11px; line-height: 14px; color: #111;
  }
  .features li::before { content: "•"; }

  .more-details {
    position: absolute; left: 42px; top: 775px;
    font-family: "Roboto Condensed", sans-serif; font-weight: 700;
    font-size: 14px; color: var(--white);
  }

  .footer-band {
    position: absolute; left: 0; top: 872px; width: 744px; height: 93px;
    background: var(--orange-box);
  }
  .footer-map {
    position: absolute; left: 85px; top: 0; width: 530px; height: 93px;
    background: linear-gradient(90deg, rgba(253,200,148,0.55), rgba(253,200,148,0.35) 60%, rgba(253,200,148,0));
  }
  .footer-tag {
    position: absolute; left: 64px; top: 28px;
    font-family: "Roboto Condensed", sans-serif; font-size: 26px; color: var(--white);
  }
  .footer-tag b { font-weight: 700; }
  .footer-tag em { font-style: normal; font-weight: 300; font-size: 20px; color: var(--peach-mid); }
</style>
</head>
<body>
<div class="canvas">
  <main class="poster">
    <header class="brand">
      <div class="brand-mark"></div>
      <div class="brand-name">Vexora</div>
    </header>

    <div class="world-map" role="img" aria-label="Dotted world map in orange tones"></div>

    <h1 class="headline">Pick up this phone NOW,<br>to keep talking…</h1>

    <section class="offer">
      <div class="offer-box box-save"><strong>SAVE 80%</strong><span>on<br>international<br>roaming</span></div>
      <div class="operator op-1">+</div>
      <div class="offer-box box-local"><strong>Get a<br>LOCAL</strong><span>number</span></div>
      <div class="operator op-2">+</div>
      <div class="offer-box box-intl"><strong>60 FREE</strong><span>minutes of<br>international<br>Calls</span></div>
      <div class="operator op-3">+</div>
      <div class="offer-box box-localmin"><strong>60 FREE</strong><span>minutes<br>of local<br>calls</span></div>
      <div class="operator op-4">=</div>
      <div class="offer-box box-price"><strong>499 BHT</strong></div>
    </section>

    <ul class="features">
      <li>Itemized bill on checkout</li>
      <li>Flexible tariff plans to choose fromExcellent call quality</li>
    </ul>

    <p class="more-details">Refer to the brochure for more details</p>

    <footer class="footer-band">
      <div class="footer-map" role="img" aria-label="Faint dotted world map strip"></div>
      <div class="footer-tag"><b>Vexora</b> <em>Keep Talking.</em></div>
    </footer>
  </main>
</div>
</body>
</html>
```